IRON PEAK TRAINING- Shooting Range!!!And virtual shooting range!!!

We are looking to do a clean cut web page for shooting range. We have indoor shooting simulator, retail store that sales accessories and pistols, rifles and shot guns. We are membership based for indoor shooting range Only and virtual shooting is open to public as well as retail store. We also specialize in shooting training classes and CWP classes.
Updates

Thank you for your patience. We are working with a busy travel schedule. We will be making final decisions tomorrow and moving forward with getting this launched. Regards, Gerald

Target Market(s)

Public and private entertainment

Industry/Entity Type

Training

Number of Pages Required

5+ page

Font styles to use
Sans Serif

Requirements
Must have
• Clean and easy approach we really like the website our friend has www.valormarkline.com please take a look at a lay out. We would like to also add onli member schedule that is available for shooting sections and that they can access and book them selvs.
Nice to have
• White, black, gray or red colors

```html
<!DOCTYPE html>
<html lang="en">
<head>
<meta charset="utf-8">
<title>Iron Peak Training – Shooting Range</title>
<link rel="stylesheet" href="https://fonts.googleapis.com/css2?family=Mulish:ital,wght@0,400;0,500;0,600;1,400&display=swap">
<style>
:root{
  --red:#c8102e;
  --ink:#2b2b2b;
  --text:#555;
  --rule:#cfcfcf;
  --dark:#2e2e2e;
  --footer:#333;
  --light:#ececec;
  --white:#fff;
}
*{box-sizing:border-box;margin:0;padding:0}
html,body{width:926px;height:1200px;overflow:hidden;background:var(--white)}
body{position:relative;font-family:"Mulish",sans-serif;color:var(--text)}
.abs{position:absolute}

/* header */
.site-header{position:absolute;left:0;top:0;width:926px;height:101px;border-bottom:1px solid #ddd;box-shadow:0 1px 3px rgba(0,0,0,.08)}
.brand{left:58px;top:34px;display:flex;align-items:center;gap:8px}
.brand-mark{width:22px;height:22px;background:var(--red);border-radius:50%}
.brand-name{font-size:14px;font-weight:600;color:var(--ink);letter-spacing:.5px;line-height:1.15}
.account-links{right:58px;top:23px;font-size:9px;color:var(--ink);display:flex;gap:10px}
.account-links .sep{color:#888}
.account-links .price{color:var(--red)}
.main-nav{left:371px;top:59px;width:498px;height:34px;background:var(--red);display:flex;justify-content:space-around;align-items:center;padding:0 6px}
.main-nav a{color:var(--white);font-size:10px;text-decoration:none;letter-spacing:.2px}

/* hero */
.hero{left:58px;top:109px;width:811px;height:314px;background:linear-gradient(100deg,#a9a7a2 0%,#8b8984 35%,#3a3d45 60%,#2a2d36 80%,#8fa24a 100%)}
.hero-caption{left:58px;top:323px;width:608px;height:70px;background:rgba(25,25,25,.85);color:var(--white);font-size:23px;line-height:30px;padding:5px 14px}
.hero-dots{left:774px;top:381px;display:flex;gap:8px}
.hero-dots span{width:10px;height:10px;border-radius:50%;background:#111}
.hero-dots span.active{background:var(--red)}

/* content */
.section-title{font-size:17.5px;font-weight:500;color:var(--ink);letter-spacing:.3px}
.section-title em{font-style:normal;color:var(--red)}
.body-copy{font-size:9.4px;line-height:17.6px;color:var(--text)}
.rule{height:1px;background:var(--rule);width:603px;left:58px}

.service{width:186px}
.service .photo{width:186px;height:121px;border:1px solid #bbb}
.service h3{font-size:13.5px;font-weight:500;color:var(--ink);margin-top:14px}
.service h3 em{font-style:normal;color:var(--red)}
.service p{font-size:9.4px;line-height:14.5px;margin-top:4px}
.service .more{display:block;font-size:9.6px;color:var(--ink);margin-top:11px;text-decoration:none}

.store-photo{left:58px;top:971px;width:186px;height:124px;border:1px solid #bbb;background:linear-gradient(135deg,#f2f2f2,#cfcfcf 60%,#e8e8e8)}
.btn-red{left:264px;top:1067px;width:86px;height:28px;background:var(--red);color:var(--white);font-size:10.5px;display:flex;align-items:center;justify-content:center}

/* sidebar */
.bookings{left:682px;top:449px;width:187px;height:337px;background:var(--red);padding:12px 15px}
.bookings h2{font-size:17px;font-weight:500;color:var(--white);line-height:19px;letter-spacing:.5px}
.field{position:absolute;left:15px;width:157px;height:28px;background:var(--white);border:1px solid #ddd;font-size:9.6px;color:#888;padding:7px 9px}
.field.select::after{content:"";position:absolute;right:9px;top:12px;border:4px solid transparent;border-top:4px solid #999}
.submit{position:absolute;left:92px;top:298px;width:80px;height:27px;background:var(--dark);color:var(--white);font-size:9.6px;display:flex;align-items:center;justify-content:center}

.testimonials{left:682px;top:800px;width:187px;height:168px;background:var(--dark);padding:16px 15px}
.testimonials h2{font-size:17px;font-weight:500;color:var(--white);letter-spacing:.5px}
.testimonials blockquote{font-size:9.4px;font-style:italic;line-height:16.4px;color:#aaa;margin-top:7px}
.testimonials cite{display:block;font-size:9.4px;color:#ddd;margin-top:8px}

.connect{left:682px;top:982px;width:187px;height:100px;background:linear-gradient(#f0f0f0,#e2e2e2);padding:15px 15px}
.connect h2{font-size:17px;font-weight:500;color:var(--ink);letter-spacing:.5px}
.social{display:flex;gap:3px;margin-top:9px}
.social span{width:29px;height:29px;border-radius:50%}

/* footer */
.site-footer{left:0;top:1123px;width:926px;height:77px;background:var(--footer)}
.footer-nav{display:flex;justify-content:center;gap:29px;margin-top:22px}
.footer-nav a{font-size:9.6px;color:#bbb;text-decoration:none}
.copyright{text-align:center;font-size:9.4px;color:#ddd;margin-top:11px}
</style>
</head>
<body>

<header class="site-header">
  <div class="abs brand"><span class="brand-mark"></span><span class="brand-name">IRON PEAK<br>TRAINING</span></div>
  <div class="abs account-links"><span>LOG IN</span><span class="sep">|</span><span>REGISTER</span><span class="sep">|</span><span>MY CART <span class="price">$ 0.00</span></span></div>
  <nav class="abs main-nav">
    <a href="#">HOME</a><a href="#">ABOUT</a><a href="#">CLASSES</a><a href="#">LOCATIONS</a><a href="#">IP STORE</a><a href="#">RANGE</a><a href="#">CONTACT US</a>
  </nav>
</header>

<div class="abs hero" role="img" aria-label="Shooter with ear protection aiming a shotgun at a paper target on an outdoor range"></div>
<div class="abs hero-caption">We have indoor shooting simulator, retail store that sales accessories and pistols, rifles and shot guns.</div>
<div class="abs hero-dots"><span class="active"></span><span></span><span></span><span></span></div>

<main>
  <h2 class="abs section-title" style="left:58px;top:445px">WELCOME TO <em>IRON PEAK</em></h2>
  <p class="abs body-copy" style="left:58px;top:471px;width:603px">Aliquam molestie, mi et imperdiet euismod, dui purus auctor tellus, et interdum lacus lectus et ante. Sed accumsan sollicitudin sapien, sit amet adipiscing turpis gravida ac. In congue, neque ac lobortis volutpat, libero mauris varius mi, vitae suscipit ipsum ligula vitae risus. Duis aliquam nibh a dui iaculis viverra id a velit. Vivamus egestas risus in magna varius commodo. Sed semper viverra egestas. Etiam pretium porttitor lectus, vel ornare neque porta volutpat.</p>

  <div class="abs rule" style="top:567px"></div>

  <h2 class="abs section-title" style="left:58px;top:587px">WHAT WE <em>DO</em></h2>
  <p class="abs body-copy" style="left:58px;top:613px;width:603px">Aliquam molestie, mi et imperdiet euismod, dui purus auctor tellus, et interdum lacus lectus et ante. Sed accumsan sollicitudin sapien, sit amet adipiscing turpis gravida ac.</p>

  <article class="abs service" style="left:58px;top:665px">
    <div class="photo" role="img" aria-label="Man in ear protection firing a pistol at an indoor range" style="background:linear-gradient(135deg,#b06a3c,#6e5442 55%,#2c3040)"></div>
    <h3>Indoor <em>Shooting Classes</em></h3>
    <p>Aliquam molestie, mi et imperdiet euisod, dui purus auctor tellus, et interdum lacus lectus et ante.</p>
    <a class="more" href="#">READ MORE</a>
  </article>
  <article class="abs service" style="left:266px;top:665px">
    <div class="photo" role="img" aria-label="Shooter in camouflage aiming a rifle down a dark range lane" style="background:linear-gradient(135deg,#4e5a38,#3a3a36 50%,#222)"></div>
    <h3>CWP&nbsp; <em>Shooting Classess</em></h3>
    <p>Aliquam molestie, mi et imperdiet euisod, dui purus auctor tellus, et interdum lacus lectus et ante.</p>
    <a class="more" href="#">READ MORE</a>
  </article>
  <article class="abs service" style="left:474px;top:665px">
    <div class="photo" role="img" aria-label="Two tactical trainees aiming pistols in a simulator room" style="background:linear-gradient(135deg,#3a3c40,#1c1d20 55%,#2e3034)"></div>
    <h3>Virtual&nbsp; <em>Shooting</em></h3>
    <p>Aliquam molestie, mi et imperdiet euisod, dui purus auctor tellus, et interdum lacus lectus et ante.</p>
    <a class="more" href="#">READ MORE</a>
  </article>

  <div class="abs rule" style="top:915px"></div>

  <h2 class="abs section-title" style="left:58px;top:935px">RETAIL <em>STORE</em></h2>
  <div class="abs store-photo" role="img" aria-label="Pistol, ear muffs, magazine and safety glasses on white"></div>
  <p class="abs body-copy" style="left:264px;top:967px;width:392px;line-height:16.5px">Aliquam molestie, mi et imperdiet euismod, dui purus auctor tellus, et interdum lacus lectus et ante. Sed accumsan sollicitudin sapien, sit amet adipiscing turpis gravida ac. In congue, neque ac lobortis volutpat, libero mauris varius mi, vitae suscipit ipsum ligula vitae risus. Duis aliquam nibh a dui iaculis viverra id a velit. Vivamus egestas risus in magna varius commodo. Sed semper viverra egestas.</p>
  <a class="abs btn-red">SHOP NOW</a>
</main>

<aside>
  <section class="abs bookings">
    <h2>MEMBER<br>BOOKINGS</h2>
    <div class="field" style="top:57px">Name</div>
    <div class="field" style="top:91px">Email Address</div>
    <div class="field" style="top:125px">Contact No.</div>
    <div class="field select" style="top:159px">Select Session</div>
    <div class="field" style="top:194px;height:94px">Enter Details</div>
    <div class="submit">SUBMIT NOW</div>
  </section>

  <section class="abs testimonials">
    <h2>TESTIMONIALS</h2>
    <blockquote>“ Aliquam molestie, mi et imperdiet euismod, dui purus auctor tellus, et interdum lacus lectus et ante. Sed accumsan sollicitudin sapien, sit amet adipiscing turpis....</blockquote>
    <cite>-Name Goes Here</cite>
  </section>

  <section class="abs connect">
    <h2>CONNECT US</h2>
    <div class="social">
      <span style="background:#3b5591"></span>
      <span style="background:#2fa39a"></span>
      <span style="background:#7a5c3e"></span>
      <span style="background:#c9302c"></span>
    </div>
  </section>
</aside>

<footer class="abs site-footer">
  <nav class="footer-nav">
    <a href="#">HOME</a><a href="#">ABOUT</a><a href="#">CLASSES</a><a href="#">LOCATIONS</a><a href="#">IP STORE</a><a href="#">RANGE</a><a href="#">CONTACT US</a>
  </nav>
  <p class="copyright">Copyright © 2015.Company Name.All Right Reserved</p>
</footer>

</body>
</html>
```